Veranix - Solution provider in business consulting

Veranix is a swiss based company providing solutions for developing markets. The business covers various fields of business consulting, such as supply chain, product costs, quality management and manufacturing management. The Business operates in a efficient, straight and solution oriented manner.
The final design should communicate these characteristics. Asian people as well as as western people shall identify the qualities of the company at first sight.
The customer needs business cards with a simple view but an recognizable design, printed in high quality. Engraved elements such as the globe or simple words are possible.
Available colors are: (RAL)
102/102/102
51/102/102
153/204/153
255/102/51
Font: Calibri

```html
<!DOCTYPE html>
<html lang="en">
<head>
<meta charset="utf-8">
<title>Veranix business cards</title>
<link rel="stylesheet" href="https://fonts.googleapis.com/css2?family=Open+Sans:wght@300;400;600;700&display=swap">
<style>
  :root {
    --stage: #ececea;
    --card-grey: #666666;
    --frost: #d6d6d4;
    --frost-ink: #666666;
    --white: #ffffff;
    --shadow: rgba(0,0,0,0.18);
  }
  * { margin: 0; padding: 0; box-sizing: border-box; }
  html, body { width: 1200px; height: 900px; overflow: hidden; }
  body {
    background: var(--stage);
    font-family: "Open Sans", Calibri, sans-serif;
    position: relative;
  }
  .card { position: absolute; box-shadow: 0 4px 14px var(--shadow); }

  /* Front card */
  .card-front { left: 78px; top: 35px; width: 587px; height: 362px; }
  .front-brand {
    height: 183px; background: var(--frost);
    display: flex; align-items: center; justify-content: center; gap: 14px;
    padding-top: 6px;
  }
  .wordmark { font-weight: 300; letter-spacing: 1px; line-height: 1; }
  .front-brand .wordmark { font-size: 58px; color: var(--frost-ink); }
  .brand-dot { border-radius: 50%; }
  .front-brand .brand-dot { width: 22px; height: 22px; background: var(--frost-ink); }

  .front-info {
    height: 179px; background: var(--card-grey); color: var(--white);
    position: relative;
  }
  .contact-list {
    position: absolute; right: 315px; top: 52px;
    list-style: none; text-align: right; font-size: 15px; line-height: 22px;
  }
  .contact-list li { display: flex; justify-content: flex-end; align-items: center; gap: 9px; }
  .contact-list svg { width: 12px; height: 12px; fill: var(--white); flex: none; }
  .person { position: absolute; left: 296px; top: 42px; font-size: 15px; line-height: 22px; }
  .person-name { font-size: 20px; font-weight: 600; line-height: 26px; }
  .person-role { margin-bottom: 18px; }

  /* Back card */
  .card-back {
    left: 389px; top: 505px; width: 565px; height: 352px;
    background: var(--card-grey); color: var(--white);
  }
  .back-brand {
    position: absolute; left: 0; right: 0; top: 145px;
    display: flex; align-items: center; justify-content: center; gap: 14px;
  }
  .back-brand .wordmark { font-size: 56px; color: var(--white); }
  .back-brand .brand-dot { width: 22px; height: 22px; background: var(--white); }
  .back-web {
    position: absolute; left: 0; right: 0; top: 286px;
    text-align: center; font-size: 15px; font-weight: 700;
  }
</style>
</head>
<body>

<section class="card card-front">
  <div class="front-brand">
    <span class="wordmark">veranix</span>
    <span class="brand-dot"></span>
  </div>
  <div class="front-info">
    <ul class="contact-list">
      <li>+41 79 555 0142
        <svg viewBox="0 0 12 12" aria-hidden="true"><path d="M3 0h6a1 1 0 0 1 1 1v10a1 1 0 0 1-1 1H3a1 1 0 0 1-1-1V1a1 1 0 0 1 1-1zm0 1.5v7.5h6V1.5z"/></svg></li>
      <li>+41 71 555 0187
        <svg viewBox="0 0 12 12" aria-hidden="true"><path d="M2.5 0.5l2 2.2-1 1.6c.8 1.6 2 2.8 3.6 3.6l1.6-1 2.2 2-1 2.1C5.3 10.8 1.2 6.7 .4 1.5z"/></svg></li>
      <li>marco.feller@veranix.ch
        <svg viewBox="0 0 12 12" aria-hidden="true"><path d="M0 2h12v8H0zm1 1v.4l5 3.2 5-3.2V3z"/></svg></li>
      <li>www.veranix.ch
        <svg viewBox="0 0 12 12" aria-hidden="true"><circle cx="6" cy="6" r="6"/></svg></li>
    </ul>
    <div class="person">
      <p class="person-name">Marco Feller</p>
      <p class="person-role">CEO</p>
      <p>Veranix GmbH Talstrasse 14</p>
      <p>9246 Feldau Switzerland</p>
    </div>
  </div>
</section>

<section class="card card-back">
  <div class="back-brand">
    <span class="wordmark">veranix</span>
    <span class="brand-dot"></span>
  </div>
  <p class="back-web">www.veranix.ch</p>
</section>

</body>
</html>
```